Creative, fresh business card design for Ripplecraft Facades

We need a fresh, creative business card design for Ripplecraft Facades. We are the manufacturer of Ripplecraft Facades in Australia. Wall panels are 2400 x 1200mm panels made from MDF and feature 3D patterns on the face of the panel. The colours to be used are green, silver/grey and white RGB
Red 187
Green 207
Blue 65.

An idea is to possibly use a watermark of one of our designs as a background (like on the "Grids" design on the left hand side of page 2 of our brochure).

Target Market(s)

Interior designers, architects, builders and home renovators

Industry/Entity Type

Business

Contact Information for Business Card

Details to go on the card are:
Our logo (attached),
Slogan: "Decorative panels for interiors and exteriors",
Contact name,
Position,
Mobile phone number,
Business address,
Business phone,
Business fax,
Website and
Email address.

I have attached a few images of our panels and our brochure for reference.

The colours of the business card should feature our logo colours which are: RGB
Red 187
Green 207
Blue 65

Requirements
Must have
• Very modern fonts and design. Some of the designs shown especially the "Prisms" design which is a popular design.
Nice to have
• Creative but simple design. Very contemporary.
Should not have
• Anything ornate or old fashioned.

```html
<!DOCTYPE html>
<html lang="en">
<head>
<meta charset="utf-8">
<title>Ripplecraft Facades – Business Card</title>
<link rel="stylesheet" href="https://fonts.googleapis.com/css2?family=Lato:wght@400;700&family=Questrial&display=swap">
<style>
  :root {
    --brand-green: rgb(187, 207, 65);
    --brand-grey: #8e8f93;
    --grey-dark: #7b7c80;
    --card-white: #f7f7f7;
    --ripple-light: #ececec;
    --ripple-shade: #dcdcdc;
    --stage: #e4e4e6;
    --text-white: #ffffff;
  }
  * { box-sizing: border-box; margin: 0; padding: 0; }
  html, body { width: 1200px; height: 900px; overflow: hidden; }
  body {
    background: var(--stage);
    font-family: "Lato", Arial, sans-serif;
    position: relative;
  }
  .card {
    position: absolute;
    left: 250px;
    width: 700px;
    height: 400px;
    background: var(--card-white);
    box-shadow: 0 6px 18px rgba(0,0,0,0.12);
    overflow: hidden;
  }
  .card--back { top: 33px; }
  .card--front { top: 467px; }

  .ripple-texture {
    position: absolute;
    background: linear-gradient(160deg, var(--ripple-light) 0%, var(--card-white) 35%, var(--ripple-shade) 60%, var(--card-white) 85%, var(--ripple-light) 100%);
  }
  .card--back .ripple-texture { inset: 20px; }
  .card--front .ripple-texture { left: 280px; top: 30px; right: 30px; height: 155px; }

  .brand {
    display: flex;
    align-items: center;
    gap: 14px;
  }
  .brand__square {
    width: 46px; height: 46px;
    background: var(--brand-green);
    flex: none;
  }
  .brand__name {
    font-family: "Lato", Arial, sans-serif;
    font-weight: 700;
    color: var(--brand-grey);
    font-size: 30px;
    line-height: 1.05;
  }
  .card--back .brand {
    position: absolute;
    left: 50%; top: 50%;
    transform: translate(-50%, -50%);
  }
  .card--back .brand__name { font-size: 36px; }
  .card--back .brand__square { width: 56px; height: 56px; }

  .contact-person {
    position: absolute;
    left: 30px; top: 30px;
    width: 240px; height: 160px;
    background: var(--brand-grey);
    color: var(--text-white);
    padding: 30px 0 0 34px;
  }
  .contact-person__name { font-weight: 700; font-size: 17px; }
  .contact-person__role { font-size: 16px; margin-top: 1px; }
  .contact-person__mobile { font-size: 17px; margin-top: 22px; letter-spacing: 0.5px; }

  .card--front .brand {
    position: absolute;
    left: 30px; top: 200px;
    width: 240px; height: 112px;
  }
  .card--front .brand__name { font-size: 26px; }

  .contact-details {
    position: absolute;
    left: 280px; top: 195px;
    width: 390px; height: 117px;
    background: var(--brand-green);
    color: var(--text-white);
    padding: 14px 0 0 20px;
    font-size: 14.5px;
    line-height: 1.45;
  }
  .contact-details__phones { font-size: 15.5px; }
  .contact-details__phones b { font-weight: 700; }
  .contact-details__web { font-weight: 700; }

  .slogan {
    position: absolute;
    left: 30px; right: 30px; top: 332px;
    font-family: "Questrial", "Century Gothic", sans-serif;
    color: var(--brand-grey);
    font-size: 20px;
    letter-spacing: 4px;
    white-space: nowrap;
  }
</style>
</head>
<body>
  <section class="card card--back" aria-label="Business card, back">
    <div class="ripple-texture" role="img" aria-label="Faint embossed ripple panel texture"></div>
    <div class="brand">
      <span class="brand__square"></span>
      <span class="brand__name">Ripplecraft<br>Facades</span>
    </div>
  </section>

  <section class="card card--front" aria-label="Business card, front">
    <div class="ripple-texture" role="img" aria-label="Faint embossed ripple panel texture"></div>

    <div class="contact-person">
      <p class="contact-person__name">Marcus Ellwood</p>
      <p class="contact-person__role">managing director</p>
      <p class="contact-person__mobile">M 0400 318 552</p>
    </div>

    <div class="brand">
      <span class="brand__square"></span>
      <span class="brand__name">Ripplecraft<br>Facades</span>
    </div>

    <div class="contact-details">
      <p class="contact-details__phones">P <b>02 9100 3810</b>&nbsp;&nbsp;F <b>02 9100 3811</b></p>
      <p>14 Harbour Lane, Kellyville NSW 2155</p>
      <p>sales@ripplecraftfacades.com.au</p>
      <p class="contact-details__web">www.ripplecraftfacades.com.au</p>
    </div>

    <p class="slogan">decorative panels for interiors &amp; exteriors</p>
  </section>
</body>
</html>
```